Etiketten-Design für Roséwein & Weißwein
Zielgruppe
Wir sind eine Weinkellerei, die einfache Trinkweine für den LEH herstellt.
Unsere Zielgruppen sind Personen ab 16 Jahren.
Aufgabenstellung
Das Etikett sollte ein Pulvereffekt mit Wasserfarbe sein.
Sorten Roséwein und Weißwein
Gerne können Sie auch Ihren kreativen Gedanken freien Lauf lassen und etwas eigenes designen.

```html
<!DOCTYPE html>
<html lang="de">
<head>
<meta charset="utf-8">
<title>Weisswein Etiketten</title>
<link href="https://fonts.googleapis.com/css2?family=Oswald:wght@400;500&family=Montserrat:wght@800&family=Mrs+Saint+Delafield&display=swap" rel="stylesheet">
<style>
  :root {
    --backdrop: #767b86;
    --label-black: #000000;
    --text-white: #ffffff;
    --wein-white: rgba(235, 235, 235, 0.82);
    --pink: #e8267a;
    --hot-pink: #ff4f9a;
    --violet: #8a4fe0;
    --blue: #4a5ad8;
    --red: #e01f2a;
    --orange: #ff6a14;
    --maroon: #3a0716;
  }
  * { margin: 0; padding: 0; box-sizing: border-box; }
  html, body { width: 740px; height: 1200px; overflow: hidden; }
  body { background: var(--backdrop); position: relative; font-family: "Oswald", sans-serif; }

  .label {
    position: absolute;
    width: 179px; height: 238px;
    background: var(--label-black);
    overflow: hidden;
    color: var(--text-white);
  }
  .label--a { left: 64px;  top: 297px; }
  .label--b { left: 277px; top: 297px; }
  .label--c { left: 486px; top: 297px; }
  .label--d { left: 65px;  top: 571px; }
  .label--e { left: 277px; top: 571px; }
  .label--f { left: 486px; top: 571px; background: var(--maroon); }

  .powder { position: absolute; inset: 0; }
  .powder--violet {
    background:
      radial-gradient(ellipse 32% 16% at 80% 56%, rgba(74,90,216,.9), transparent 70%),
      radial-gradient(ellipse 30% 15% at 58% 60%, rgba(190,90,230,.85), transparent 70%),
      radial-gradient(ellipse 26% 12% at 36% 57%, rgba(255,79,154,.85), transparent 70%),
      radial-gradient(ellipse 14% 8% at 22% 52%, rgba(224,31,42,.7), transparent 70%);
  }
  .powder--violet-low {
    background:
      radial-gradient(ellipse 32% 16% at 80% 60%, rgba(74,90,216,.9), transparent 70%),
      radial-gradient(ellipse 30% 15% at 58% 64%, rgba(190,90,230,.85), transparent 70%),
      radial-gradient(ellipse 26% 12% at 36% 60%, rgba(255,79,154,.85), transparent 70%),
      radial-gradient(ellipse 14% 8% at 22% 55%, rgba(224,31,42,.7), transparent 70%);
  }
  .powder--crimson {
    background:
      radial-gradient(ellipse 30% 18% at 12% 36%, rgba(255,170,200,.85), transparent 72%),
      radial-gradient(ellipse 55% 26% at 45% 45%, rgba(232,38,122,.95), transparent 72%),
      radial-gradient(ellipse 40% 18% at 80% 52%, rgba(224,31,42,.85), transparent 72%),
      radial-gradient(ellipse 30% 22% at 92% 88%, rgba(255,106,20,.95), transparent 70%),
      radial-gradient(ellipse 20% 12% at 72% 80%, rgba(224,31,42,.8), transparent 70%);
  }
  .powder--dust {
    background:
      radial-gradient(ellipse 70% 14% at 55% 28%, rgba(255,120,170,.85), transparent 75%),
      radial-gradient(ellipse 80% 30% at 50% 45%, rgba(200,40,100,.55), transparent 75%),
      linear-gradient(180deg, #1a0209 0%, #5a1028 35%, #3a0716 70%, #240410 100%);
  }

  .logo {
    position: absolute; top: 12px; left: 0; right: 0;
    text-align: center; font-size: 7px; letter-spacing: 1.5px;
  }
  .script {
    position: absolute; font-family: "Mrs Saint Delafield", cursive;
    line-height: 1; color: var(--text-white);
  }
  .script--weiss { left: 24px; top: 26px; font-size: 64px; }
  .script--wein  { left: 70px; top: 76px; font-size: 64px; }
  .script--solo  { left: 28px; top: 42px; font-size: 80px; }
  .block-wein {
    position: absolute; left: 0; right: 0; top: 84px;
    text-align: center; font-family: "Montserrat", sans-serif;
    font-weight: 800; font-size: 47px; letter-spacing: -1px;
    color: var(--wein-white); line-height: 1;
  }
  .variety {
    position: absolute; left: 0; right: 0; top: 172px;
    text-align: center; font-size: 13.5px; font-weight: 500; letter-spacing: 1.5px;
  }
  .style {
    position: absolute; left: 0; right: 0; top: 193px;
    text-align: center; font-size: 6.5px; letter-spacing: 1.2px;
  }
  .facts {
    position: absolute; left: 8px; right: 9px; bottom: 7px;
    display: flex; justify-content: space-between;
    font-size: 9px; font-weight: 500;
  }
</style>
</head>
<body>

<section class="label label--a">
  <div class="powder powder--violet" role="img" aria-label="Farbpulverwolke in Rot, Pink, Violett und Blau"></div>
  <div class="logo">LOGO</div>
  <div class="script script--weiss">Weiss</div>
  <div class="script script--wein">Wein</div>
  <div class="variety">WEISSWEIN</div>
  <div class="style">- TROCKEN -</div>
  <div class="facts"><span>12,5% ALC/VOL</span><span>750 ML</span></div>
</section>

<section class="label label--b">
  <div class="powder powder--crimson" role="img" aria-label="Farbpulverexplosion in Pink, Rot und Orange"></div>
  <div class="logo">LOGO</div>
  <div class="script script--weiss">Weiss</div>
  <div class="script script--wein">Wein</div>
  <div class="variety">WEISSWEIN</div>
  <div class="style">- TROCKEN -</div>
  <div class="facts"><span>12,5% ALC/VOL</span><span>750 ML</span></div>
</section>

<section class="label label--c">
  <div class="powder powder--crimson" role="img" aria-label="Farbpulverexplosion in Pink, Rot und Orange"></div>
  <div class="logo">LOGO</div>
  <div class="script script--weiss">Weiss</div>
  <div class="block-wein">WEIN</div>
  <div class="variety">WEISSWEIN</div>
  <div class="style">- TROCKEN -</div>
  <div class="facts"><span>12,5% ALC/VOL</span><span>750 ML</span></div>
</section>

<section class="label label--d">
  <div class="powder powder--violet-low" role="img" aria-label="Farbpulverwolke in Rot, Pink, Violett und Blau"></div>
  <div class="logo">LOGO</div>
  <div class="script script--solo">Weiss</div>
  <div class="variety">WEISSWEIN</div>
  <div class="style">- TROCKEN -</div>
  <div class="facts"><span>12,5% ALC/VOL</span><span>750 ML</span></div>
</section>

<section class="label label--e">
  <div class="powder powder--violet-low" role="img" aria-label="Farbpulverwolke in Rot, Pink, Violett und Blau"></div>
  <div class="logo">LOGO</div>
  <div class="script script--weiss">Weiss</div>
  <div class="block-wein">WEIN</div>
  <div class="variety">WEISSWEIN</div>
  <div class="style">- TROCKEN -</div>
  <div class="facts"><span>12,5% ALC/VOL</span><span>750 ML</span></div>
</section>

<section class="label label--f">
  <div class="powder powder--dust" role="img" aria-label="Feiner pinkfarbener Pulverstaub auf dunklem Weinrot"></div>
  <div class="logo">LOGO</div>
  <div class="script script--weiss">Weiss</div>
  <div class="block-wein">WEIN</div>
  <div class="variety">WEISSWEIN</div>
  <div class="style">- TROCKEN -</div>
  <div class="facts"><span>12,5% ALC/VOL</span><span>750 ML</span></div>
</section>

</body>
</html>
```